Website for International Non-Profit for Birth Parent Searching

LumaKin is a 501(c)(3) non-profit organization that helps Chinese adoptees search and reunite with birth families who were separated due the One Child Policy in China. We want to create a website that can link to an information database that allows website users to easily access information around search ads in an organized way; help connect families to professional searchers; provide resources for community support for adoptees and their families as they embark on a personal and emotional journey of finding birth family through support groups on social media and consultation/education on the searching process; and provide the opportunity for the adoptive community to give back through donations and volunteer opportunities. The final design should foster a sense of community and be easy navigable to access the multiple resources we provide to help families search for each other. We would like to see designs with red/black/white color schemes that are gentle, inviting, and family friendly to viewers. We would like to see some design layouts with Chinese themes, if possible.

```html
<!DOCTYPE html>
<html lang="en">
<head>
<meta charset="utf-8">
<title>LumaKin — Start Your Search</title>
<link href="https://fonts.googleapis.com/css2?family=Lato:wght@400;700;900&family=Roboto:wght@400;500&display=swap" rel="stylesheet">
<style>
:root{
  --red:#a3000f;
  --red-bright:#c8101e;
  --ink:#111111;
  --text:#3a3a3a;
  --white:#ffffff;
  --blush:#f6e0e0;
  --panel:#f0efee;
  --line:#a9a9a9;
  --footer:#0c0c0c;
}
*{margin:0;padding:0;box-sizing:border-box}
html,body{width:1200px;height:2902px;overflow:hidden}
body{position:relative;background:var(--white);font-family:'Lato',sans-serif;color:var(--ink)}
.abs{position:absolute}

/* header */
.site-header{position:absolute;left:0;top:0;width:1200px;height:90px;background:var(--white);z-index:3}
.brand-badge{position:absolute;left:66px;top:-8px;width:180px;height:180px;border-radius:50%;background:var(--white);z-index:4;display:flex;align-items:center;justify-content:center}
.brand-badge span{font-weight:700;font-size:30px;color:var(--red-bright)}
.main-nav{position:absolute;top:33px;left:304px;display:flex;gap:0;font-size:15px;font-weight:700;letter-spacing:-.2px}
.main-nav a{position:absolute;white-space:nowrap;color:var(--ink);text-decoration:none}
.main-nav a.active{color:var(--red-bright)}
.caret{display:inline-block;width:7px;height:7px;border-right:2px solid var(--ink);border-bottom:2px solid var(--ink);transform:rotate(45deg);margin-left:12px;position:relative;top:-3px}
.donate-btn{position:absolute;left:925px;top:20px;width:149px;height:42px;background:var(--red);color:var(--white);font-size:14px;font-weight:700;display:flex;align-items:center;justify-content:center;border-radius:3px}
.lang{position:absolute;left:1094px;top:33px;font-size:15px;font-weight:700}

/* hero */
.hero-photo{position:absolute;left:0;top:90px;width:1200px;height:390px;background:linear-gradient(100deg,#6d7b74 0%,#c9c4bd 28%,#ece9e4 45%,#8e9592 70%,#4d5755 100%)}
.hero-curve{position:absolute;left:0;top:360px;width:1200px;height:130px}

/* intro */
.side-menu{position:absolute;left:144px;top:556px;width:249px;height:276px;background:var(--red);color:var(--white);padding:18px 0 0 22px}
.side-menu li{list-style:none;height:31px;font-size:16px;display:flex;align-items:center}
.side-menu li.main{font-weight:700}
.side-menu li.sub{padding-left:41px;font-size:15.5px}
.bullet{width:13px;height:13px;border-radius:50%;background:var(--white);margin-right:13px;position:relative}
.bullet::after{content:"";position:absolute;left:3px;top:4px;border-left:6px solid var(--red);border-top:2.5px solid transparent;border-bottom:2.5px solid transparent}
.intro-title{position:absolute;left:448px;top:562px;font-size:35px;font-weight:900;letter-spacing:-.3px}
.intro-copy{position:absolute;left:448px;top:622px;width:612px;font-size:16px;line-height:24px;color:var(--text)}

/* steps */
.steps-panel{position:absolute;left:144px;top:888px;width:913px;height:442px;background:radial-gradient(circle at 85% 20%,#f7f3f3 0%,var(--panel) 60%)}
.steps-title{position:absolute;left:0;width:857px;top:50px;text-align:center;font-size:33px;font-weight:700;letter-spacing:-.3px}
.steps-line{position:absolute;left:136px;top:221px;width:632px;height:4px;background:var(--line)}
.step-icon{position:absolute;top:142px;width:160px;height:160px;border-radius:50%;border:2px solid #8f8f8f;background:var(--white);display:flex;align-items:center;justify-content:center}
.step-label{position:absolute;width:240px;text-align:center;font-size:16px;font-weight:700;line-height:22px}

/* quote band */
.quote-band{position:absolute;left:0;top:1420px;width:1200px;height:552px;background:linear-gradient(110deg,#3e4a2c 0%,#6f7758 35%,#8d8a77 55%,#5f6848 80%,#34402a 100%)}
.quote-text{position:absolute;left:170px;top:1618px;width:860px;text-align:center;color:var(--white);font-size:25px;font-weight:700;line-height:35.5px}

/* contact */
.contact{position:absolute;left:0;top:1972px;width:1200px;height:622px;background:var(--blush)}
.contact-title{position:absolute;left:0;width:1200px;top:81px;text-align:center;font-size:34px;font-weight:900;letter-spacing:-.5px}
.contact-title em{font-style:normal;color:var(--red-bright)}
.contact-rule{position:absolute;left:563px;top:132px;width:74px;height:3px;background:var(--red-bright)}
.field{position:absolute;background:var(--white);border:1px solid #cfc3c3;box-shadow:0 1px 3px rgba(0,0,0,.18);font-family:'Roboto',sans-serif;font-size:12px;color:#333;padding:15px 0 0 17px}
.submit-btn{position:absolute;left:523px;top:505px;width:153px;height:38px;border-radius:19px;background:var(--red);color:var(--white);font-family:'Roboto',sans-serif;font-size:14px;font-weight:500;display:flex;align-items:center;justify-content:center}

/* footer */
.site-footer{position:absolute;left:0;top:2594px;width:1200px;height:308px;background:var(--footer);color:var(--white);font-family:'Roboto',sans-serif}
.footer-brand{position:absolute;left:150px;top:134px;font-family:'Lato',sans-serif;font-weight:700;font-size:34px}
.footer-nav{position:absolute;left:364px;top:72px;font-size:13px;font-weight:500}
.footer-nav span{position:absolute;white-space:nowrap}
.footer-rule{position:absolute;left:364px;top:111px;width:678px;height:1px;background:#8a8a8a}
.contact-item{position:absolute;top:140px;display:flex;gap:16px;font-size:13.5px;line-height:19px}
.contact-icon{width:29px;height:29px;background:var(--white);display:flex;align-items:center;justify-content:center;margin-top:2px}
.copyright{position:absolute;left:364px;top:206px;font-size:10.5px;letter-spacing:.2px}
</style>
</head>
<body>

<header class="site-header">
  <nav class="main-nav">
    <a style="left:0">HOME</a>
    <a style="left:72px">WHO WE ARE<i class="caret"></i></a>
    <a class="active" style="left:203px">START YOUR SEARCH</a>
    <a style="left:377px">GET INVOLVED</a>
    <a style="left:507px">RESOURCES</a>
  </nav>
  <div class="donate-btn">DONATE NOW</div>
  <div class="lang">EN<i class="caret" style="margin-left:12px;width:6px;height:6px"></i></div>
</header>
<div class="brand-badge"><span>LumaKin</span></div>

<div class="hero-photo" role="img" aria-label="Smiling young woman in a white shirt holding a clipboard by a window"></div>
<svg class="hero-curve" viewBox="0 0 1200 130" preserveAspectRatio="none">
  <path d="M0 90 C150 40 330 30 470 45 C640 62 720 110 900 110 C1020 110 1120 60 1200 10 L1200 130 L0 130 Z" fill="#ffffff"/>
  <path d="M0 90 C150 40 330 30 470 45 C640 62 720 110 900 110 C1020 110 1120 60 1200 10 L1200 12 C1120 70 1020 125 880 125 C720 125 640 78 470 65 C330 55 150 65 0 110 Z" fill="#a3000f"/>
</svg>

<ul class="side-menu">
  <li class="main"><i class="bullet"></i>Gather Information</li>
  <li class="sub">Search Database</li>
  <li class="sub">Search Ads</li>
  <li class="main"><i class="bullet"></i>Submit DNA</li>
  <li class="main"><i class="bullet"></i>Organize Your Team</li>
  <li class="sub">Private Searchers</li>
  <li class="sub">Search Volunteers</li>
  <li class="main"><i class="bullet"></i>FAQs</li>
</ul>
<h1 class="intro-title">START YOUR SEARCH</h1>
<p class="intro-copy">Sed ut perspiciatis unde omnis iste natus error sit voluptatem accusantium doloremque laudantium, totam rem aperiam, eaque ipsa quae ab illo inventore veritatis et quasi architecto beatae vitae dicta sunt explicabo. Nemo enim ipsam voluptatem quia voluptas sit aspernatur aut odit aut fugit, sed quia consequuntur magni dolores eos qui ratione voluptatem sequi nesciunt. Neque porro quisquam est, qui dolorem ipsum quia dolor sit amet, consectetur, adipisci velit, sed quia non numquam eius modi tempora incidunt ut labore et dolore magnam aliquam quaerat voluptatem. Ut enim ad minima veniam, quis nostrum exercitationem ullam</p>

<section class="steps-panel">
  <h2 class="steps-title">How we help you connect with your family</h2>
  <div class="steps-line"></div>
  <div class="step-icon" style="left:57px">
    <svg width="84" height="84" viewBox="0 0 84 84" fill="none" stroke="#222" stroke-width="2.5">
      <path d="M8 4h36l14 14v62H8z"/><path d="M44 4v14h14"/>
      <path d="M18 30h28M18 40h28M18 50h22M18 60h16M18 70h20"/>
      <path d="M48 72l22-24 6 6-22 24-8 2z"/>
    </svg>
  </div>
  <div class="step-icon" style="left:372px">
    <svg width="100" height="84" viewBox="0 0 100 84" fill="none" stroke="#222" stroke-width="2.5">
      <rect x="16" y="6" width="68" height="54" rx="3"/><rect x="22" y="12" width="56" height="42"/>
      <path d="M6 64h88v6a6 6 0 0 1-6 6H12a6 6 0 0 1-6-6z"/>
      <path d="M30 18c10 6 0 12 10 18s0 12 10 12M40 18c-10 6 0 12-10 18s0 12-10 12"/>
      <path d="M54 20h18M54 30h18M54 40h18"/>
    </svg>
  </div>
  <div class="step-icon" style="left:689px">
    <svg width="84" height="84" viewBox="0 0 84 84" fill="none" stroke="#222" stroke-width="2.5">
      <circle cx="34" cy="34" r="22"/><circle cx="34" cy="34" r="15"/>
      <path d="M50 50l22 22" stroke-width="6" stroke-linecap="round"/>
    </svg>
  </div>
  <div class="step-label" style="left:25px;top:322px">STEP 1</div>
  <div class="step-label" style="left:25px;top:357px">GATHER INFORMATION</div>
  <div class="step-label" style="left:331px;top:322px">STEP 2</div>
  <div class="step-label" style="left:331px;top:357px">SUBMIT DNA</div>
  <div class="step-label" style="left:648px;top:322px">STEP 1</div>
  <div class="step-label" style="left:648px;top:357px">ORGANIZE<br>YOUR SEARCH TEAM</div>
</section>

<div class="quote-band" role="img" aria-label="Smiling family of three sitting together on grass in a park"></div>
<p class="quote-text">"We are partnered with Qinyuan which is China's largest and most successful family search volunteer organization that utilizes a network of hundreds of thousands of volunteers to help Chinese adoptees reunite with birth family in China, free of charge. Please contact us to be connected with a Qinyuan volun-teer that corresponds with your search needs."</p>

<section class="contact">
  <h2 class="contact-title">GET <em>IN TOUCH</em></h2>
  <div class="contact-rule"></div>
  <div class="field" style="left:229px;top:177px;width:366px;height:44px">First Name</div>
  <div class="field" style="left:605px;top:177px;width:367px;height:44px">Last Name</div>
  <div class="field" style="left:229px;top:232px;width:366px;height:44px">Email address</div>
  <div class="field" style="left:605px;top:232px;width:367px;height:44px">Address</div>
  <div class="field" style="left:229px;top:288px;width:743px;height:58px">Phone number</div>
  <div class="field" style="left:229px;top:360px;width:743px;height:113px">Reason for inquiry</div>
  <div class="submit-btn">SUBMIT</div>
</section>

<footer class="site-footer">
  <div class="footer-brand">LumaKin</div>
  <nav class="footer-nav">
    <span style="left:0">HOME</span>
    <span style="left:65px">WHO WE ARE</span>
    <span style="left:174px">OUR SERVICES</span>
    <span style="left:294px">GET INVOLVED</span>
    <span style="left:412px">TOOLS AND RESOURCES</span>
    <span style="left:592px">CONTACT US</span>
  </nav>
  <div class="footer-rule"></div>
  <div class="contact-item" style="left:364px">
    <div class="contact-icon"><svg width="16" height="16" viewBox="0 0 24 24"><path fill="#c8101e" d="M6.6 10.8a15 15 0 0 0 6.6 6.6l2.2-2.2c.3-.3.7-.4 1-.2 1.1.4 2.3.6 3.6.6.6 0 1 .4 1 1V20c0 .6-.4 1-1 1A17 17 0 0 1 3 4c0-.6.4-1 1-1h3.5c.6 0 1 .4 1 1 0 1.3.2 2.5.6 3.6.1.3 0 .7-.2 1z"/></svg></div>
    <div>Phone:<br>555-014-2290</div>
  </div>
  <div class="contact-item" style="left:533px">
    <div class="contact-icon"><svg width="14" height="18" viewBox="0 0 14 20"><path fill="#c8101e" d="M7 0a7 7 0 0 0-7 7c0 5 7 13 7 13s7-8 7-13a7 7 0 0 0-7-7zm0 9.5A2.5 2.5 0 1 1 7 4.5a2.5 2.5 0 0 1 0 5z"/></svg></div>
    <div>4120 Maple Crest Drive,<br>9C, Lakewood, CO 80226</div>
  </div>
  <div class="contact-item" style="left:783px">
    <div class="contact-icon"><svg width="17" height="13" viewBox="0 0 20 15"><rect width="20" height="15" fill="#c8101e"/><path d="M1 1l9 7 9-7" stroke="#fff" stroke-width="1.6" fill="none"/></svg></div>
    <div>Email:<br>lumakincharities@mail.org</div>
  </div>
  <div class="copyright">© COPYRIGHTS 2021 LUMAKIN &nbsp;| &nbsp;&nbsp;ALL RIGHTS RESERVED</div>
</footer>

</body>
</html>
```